Business Cards Needed for Innovative Healthcare Marketing Company

We are a marketing company focused on healthcare. Our company is all about rebranding yourself renewing your image and generating results. The phoenix stands for "reborn" or "rising" which we provide new brands for our clients we take their old brands and renew it with creativity and innovation. I am looking for a business card with color dimension. I have attached an example of a card I think has the look and feel of what I am trying to accomplish. I like that the card example has black and grey font colors, I like the font placement and the small logo, I really like the use of the colors on the right those are the colors of my logo. My logo is phoenix so maybe incorporating flames similar to that design. I would like the back a solid color maybe red with an opaque version of the logo and website. As a marketing company I am always open to creative liberty!

Target Market(s)

Doctors and business professionals.

Industry/Entity Type

Marketing

Contact Information for Business Card

Valcorne Health Care Marketing
Marla Tenwick- CEO
#(512)638-2974
email-marla@valcorne.com
website- valcorne.com

Font styles to use
Sans Serif

Colors
ec1f27
f37122
ffc214
fbed22
fbf289
f04a50

Requirements
Must have
• The logo and required information
Nice to have
• icons by the information
Should not have
• child like font

```html
<!DOCTYPE html>
<html lang="en">
<head>
<meta charset="utf-8">
<title>Valcorne Health Care Marketing – Business Card</title>
<link href="https://fonts.googleapis.com/css2?family=Open+Sans:wght@300;400;700&display=swap" rel="stylesheet">
<style>
  :root {
    --backdrop: #262626;
    --card-white: #ffffff;
    --brand-red: #9f1d22;
    --deep-red: #a3202a;
    --flame-orange: #f37122;
    --amber: #f7941d;
    --ink: #4a4a4a;
  }
  * { margin: 0; padding: 0; box-sizing: border-box; }
  html, body {
    width: 1200px; height: 987px; overflow: hidden;
    background: var(--backdrop);
    font-family: "Open Sans", sans-serif;
  }
  .card {
    position: absolute; left: 293px; width: 615px; height: 352px;
    box-shadow: 0 4px 10px rgba(0,0,0,.45);
  }
  .card--front { top: 125px; background: var(--card-white); overflow: hidden; }
  .card--back { top: 511px; background: var(--brand-red); }

  .brand { position: absolute; display: flex; align-items: center; gap: 16px; }
  .brand__dot { width: 22px; height: 22px; border-radius: 50%; background: var(--flame-orange); flex: none; }
  .brand__name {
    font-weight: 300; color: var(--deep-red); line-height: 1.05;
    text-transform: uppercase;
  }
  .brand__name .line-main { display: block; font-size: 47px; letter-spacing: 1px; }
  .brand__name .line-sub { display: block; font-size: 14.5px; letter-spacing: .8px; margin-top: 6px; }
  .card--front .brand { left: 138px; top: 106px; }

  .person { position: absolute; right: 330px; top: 233px; text-align: right; }
  .person__name { font-weight: 700; font-size: 23px; color: var(--deep-red); }
  .person__role { font-weight: 700; font-size: 16px; color: var(--amber); margin-top: 2px; }

  .contact { position: absolute; left: 308px; top: 224px; list-style: none; }
  .contact__item {
    display: flex; align-items: center; gap: 6px; height: 23.5px;
    font-size: 16px; color: var(--ink);
  }
  .contact__item svg { width: 14px; height: 14px; fill: var(--deep-red); }

  .front-band {
    position: absolute; left: 0; bottom: 0; width: 100%; height: 13px;
    background: linear-gradient(90deg, var(--deep-red) 0 400px, var(--brand-red) 430px, var(--amber) 100%);
  }
  .front-band__slash {
    position: absolute; left: 398px; bottom: 0; width: 4px; height: 13px;
    background: var(--card-white); transform: skewX(-18deg);
  }

  .card--back .brand {
    left: 0; right: 0; top: 120px; justify-content: center;
  }
  .card--back .brand__name { color: var(--card-white); text-align: center; }
  .card--back .brand__name .line-main { font-size: 40px; }
  .card--back .brand__name .line-sub { font-size: 12.5px; }
</style>
</head>
<body>
  <section class="card card--front" aria-label="Business card front">
    <div class="brand">
      <span class="brand__dot"></span>
      <div class="brand__name">
        <span class="line-main">Valcorne</span>
        <span class="line-sub">Health Care Marketing</span>
      </div>
    </div>

    <div class="person">
      <div class="person__name">Marla Tenwick</div>
      <div class="person__role">CEO</div>
    </div>

    <ul class="contact">
      <li class="contact__item">
        <svg viewBox="0 0 24 24" aria-hidden="true"><path d="M6.6 10.8a15.1 15.1 0 0 0 6.6 6.6l2.2-2.2a1 1 0 0 1 1-.25 11.4 11.4 0 0 0 3.6.57 1 1 0 0 1 1 1V20a1 1 0 0 1-1 1A17 17 0 0 1 3 4a1 1 0 0 1 1-1h3.5a1 1 0 0 1 1 1c0 1.25.2 2.45.57 3.57a1 1 0 0 1-.25 1z"/></svg>
        (512)638-2974
      </li>
      <li class="contact__item">
        <svg viewBox="0 0 24 24" aria-hidden="true"><path d="M2 5h20v14H2z M3.5 6.5 12 13l8.5-6.5" fill="var(--deep-red)"/><path d="M3.5 6.5 12 13l8.5-6.5" fill="none" stroke="#fff" stroke-width="1.6"/></svg>
        marla@valcorne.com
      </li>
      <li class="contact__item">
        <svg viewBox="0 0 24 24" aria-hidden="true"><circle cx="12" cy="12" r="10"/><path d="M2 12h20M12 2c3 3 3 17 0 20M12 2c-3 3-3 17 0 20" fill="none" stroke="#fff" stroke-width="1.4"/></svg>
        www.valcorne.com
      </li>
    </ul>

    <div class="front-band"><span class="front-band__slash"></span></div>
  </section>

  <section class="card card--back" aria-label="Business card back">
    <div class="brand">
      <div class="brand__name">
        <span class="line-main">Valcorne</span>
        <span class="line-sub">Health Care Marketing</span>
      </div>
    </div>
  </section>
</body>
</html>
```